Fun, Clean Business Card For Family Focused Travel Agency

I need a business card using specific colors and fonts as in the uploaded files. Ideally, I would like a large image of the logo on the back and all the contact info on the front. Maybe the stars/dots somewhere in a flowy form.

I do want it the contact information to be clear and easy to read. I don't want it to look too busy. Maybe even a bit minimalist.

I plan or ordering the ROUNDED CORNER business cards from Cardwell Press, so please consider that in your design.

Target Market(s)

Families with children, couples, groups of friends

Contact Information for Business Card

Marla Quint, Owner
Marla@TumbleTrips.example
Cell Phone Number 555-218-4603
Office Phone Number 555-647-1925
Specializing in Glimmerland destinations, Pelican Bay Fun Park, Cruises and All-Inclusive Vacations.

Nice but not required:
www.TumbleTrips.example
Nook, Pixo, Ping icons with username: TumbleTrips

Font styles to use
Sans Serif

Requirements
Must have
• Please try to use the colors from the logo as much as possible. I understand lighter shades/colors may be needed for some things.
Should not have
• NO SERIF FONTS. That is really the only thing I do not want at all

```html
<!DOCTYPE html>
<html lang="en">
<head>
<meta charset="utf-8">
<title>TumbleTrips Business Card</title>
<link rel="stylesheet" href="https://fonts.googleapis.com/css2?family=Arimo:ital,wght@0,400;0,700;1,400&display=swap">
<style>
  :root {
    --backdrop: #32b391;
    --card: #ffffff;
    --ink: #111111;
    --navy: #1b1d38;
    --rule: #9a9a9a;
    --orange: #f07a2a;
    --peach: rgba(242, 201, 169, 0.45);
    --butter: rgba(239, 227, 160, 0.45);
    --mint: rgba(168, 220, 210, 0.45);
    --sky: rgba(196, 220, 237, 0.45);
  }
  * { margin: 0; padding: 0; box-sizing: border-box; }
  html, body { width: 1200px; height: 848px; overflow: hidden; }
  body {
    background: var(--backdrop);
    font-family: "Arimo", Arial, sans-serif;
    color: var(--ink);
    position: relative;
  }
  .card {
    position: absolute;
    background: var(--card);
    border-radius: 17px;
    overflow: hidden;
  }
  .card--back { left: 121px; top: 110px; width: 604px; height: 344px; }
  .card--front { left: 471px; top: 391px; width: 617px; height: 352px; }

  .brand {
    position: absolute;
    left: 100px; top: 134px;
    display: flex; align-items: center; gap: 18px;
  }
  .brand__dot {
    width: 28px; height: 28px; border-radius: 50%;
    background: var(--orange);
  }
  .brand__name {
    font-size: 62px; font-weight: 700; color: var(--navy);
    letter-spacing: -0.5px; line-height: 1;
  }

  .sparkle-trail {
    position: absolute;
    left: 250px; top: 190px;
    width: 330px; height: 34px;
    border-radius: 17px;
    background: linear-gradient(90deg, var(--butter), var(--mint), var(--peach), var(--sky), var(--butter), var(--mint));
    transform: rotate(-7deg);
    transform-origin: left center;
  }

  .abs { position: absolute; white-space: nowrap; line-height: 1; }
  .holder__name { left: 56px; top: 73px; font-size: 24px; font-weight: 700; }
  .holder__title { left: 56px; top: 102px; font-size: 17px; }
  .divider { position: absolute; left: 54px; top: 144px; width: 190px; height: 1px; background: var(--rule); }
  .contact { font-size: 14px; left: 54px; }
  .contact--cell { top: 167px; }
  .contact--office { top: 184px; }
  .contact--email { top: 223px; }
  .contact--web { top: 270px; }
  .handle { right: 56px; top: 73px; font-size: 18px; }
  .socials {
    position: absolute; right: 56px; top: 108px;
    display: flex; gap: 18px;
    list-style: none;
  }
  .socials__item { font-size: 13px; font-weight: 700; line-height: 1; }
  .specialties {
    position: absolute; right: 56px; top: 225px;
    text-align: right; font-style: italic; font-size: 12px; line-height: 15.5px;
  }
</style>
</head>
<body>
  <section class="card card--back" aria-label="Card back">
    <div class="brand">
      <span class="brand__dot"></span>
      <span class="brand__name">TumbleTrips</span>
    </div>
  </section>

  <section class="card card--front" aria-label="Card front">
    <div class="sparkle-trail" role="img" aria-label="Flowing trail of small pastel stars and dots"></div>

    <p class="abs holder__name">Marla Quint</p>
    <p class="abs holder__title">Owner</p>
    <span class="divider"></span>
    <p class="abs contact contact--cell">Cell: 555-218-4603</p>
    <p class="abs contact contact--office">Office:555-647-1925</p>
    <p class="abs contact contact--email">Marla@TumbleTrips.example</p>
    <p class="abs contact contact--web">www.TumbleTrips.example</p>

    <p class="abs handle">TumbleTrips</p>
    <ul class="socials" aria-label="Social profiles">
      <li class="socials__item">Ping</li>
      <li class="socials__item">Pixo</li>
      <li class="socials__item">Nook</li>
    </ul>
    <p class="specialties">Specializing in<br>Glimmerland destinations,<br>Pelican Bay Fun Park,<br>Cruises and All-Inclusive Vacations.</p>
  </section>
</body>
</html>
```